Natural Light/Organic/Documentary Photography Business

I like a simple, approachable, feminine, earthy/organic feel. Earth/neutral tones, nothing too loud or obnoxious. I like the watercolor look. I don't want anything too trendy or something I'll get tired of after a couple months. As far as colors, I am much more a fan of cream/taupe/blue/green...not a fan of pink or purple at all.

Target Market(s)

Weddings & Families

Industry/Entity Type

Wedding Photography

Contact Information for Business Card

website, email, phone number

Font styles to use
Other font styles liked:
• Horizontes, Gotham

Colors

Designer to choose colors to be used in the design.

Requirements
Must have
• Website: www.mirelhatchway.com
• Phone: 418.629.5073
• Email: mirel@mirelhatchway.com
Nice to have
• I like the watercolor look but its not necessary. I like simple/earthy tones. Nothing too loud or distracting. Simple & feminine without being too girly. I like an approachable/soft feel.
• Instagram: www.instagram.com/mirelhatchwayphotography/
Should not have
• NO loud colors or design or pattern. I do not want a photo of a camera or lens or anything cheesy like that.

```html
<!DOCTYPE html>
<html lang="en">
<head>
<meta charset="utf-8">
<title>Mirel Hatchway Photography – Business Card</title>
<link rel="stylesheet" href="https://fonts.googleapis.com/css2?family=Mrs+Saint+Delafield&family=Montserrat:wght@400;500&display=swap">
<style>
  :root {
    --page: #ffffff;
    --card: #ffffff;
    --ink: #7b716b;
    --ink-soft: #8d847e;
    --frame: #a59c95;
    --wash-warm: #e3cdb4;
    --wash-mid: #ece0d3;
    --wash-light: #f6f1ec;
  }
  * { margin: 0; padding: 0; box-sizing: border-box; }
  html, body {
    width: 1200px;
    height: 867px;
    overflow: hidden;
    background: var(--page);
  }
  .business-card {
    position: absolute;
    left: 75px;
    top: 113px;
    width: 1050px;
    height: 640px;
    background: var(--card);
  }
  .watercolor-field {
    position: absolute;
    left: 77px;
    top: 67px;
    width: 898px;
    height: 505px;
    background: linear-gradient(160deg, var(--wash-warm) 0%, var(--wash-mid) 50%, var(--wash-light) 100%);
  }
  .identity-panel {
    position: absolute;
    left: 194px;
    top: 171px;
    width: 666px;
    height: 301px;
    background: var(--card);
    border: 1px solid var(--frame);
    text-align: center;
    color: var(--ink);
  }
  .brand-name {
    position: absolute;
    left: 0;
    right: 0;
    top: 24px;
    font-family: "Mrs Saint Delafield", cursive;
    font-size: 92px;
    font-weight: 400;
    line-height: 1;
    color: var(--ink);
  }
  .brand-tagline {
    position: absolute;
    left: 0;
    right: 0;
    top: 116px;
    font-family: "Montserrat", sans-serif;
    font-size: 12px;
    letter-spacing: 7px;
    padding-left: 7px;
    color: var(--ink-soft);
  }
  .contact-list {
    position: absolute;
    left: 0;
    right: 0;
    top: 177px;
    list-style: none;
    font-family: "Montserrat", sans-serif;
    font-size: 13px;
    line-height: 25px;
    color: var(--ink-soft);
  }
  .contact-label { font-weight: 500; color: var(--ink); }
  .contact-dot { margin: 0 8px; }
</style>
</head>
<body>
  <main class="business-card">
    <div class="watercolor-field" role="img" aria-label="Soft watercolor wash in earthy sand, sage and slate tones"></div>
    <section class="identity-panel">
      <h1 class="brand-name">Mirel Hatchway</h1>
      <p class="brand-tagline">PHOTOGRAPHY</p>
      <ul class="contact-list">
        <li><span class="contact-label">Website</span> | www.mirelhatchway.com<span class="contact-dot">·</span><span class="contact-label">Phone</span> | 418 629 5073</li>
        <li><span class="contact-label">Email</span> | mirel@mirelhatchway.com</li>
        <li><span class="contact-label">Instagram</span> | @mirelhatchwayphotography</li>
      </ul>
    </section>
  </main>
</body>
</html>
```